Website Redesign using existing images, copy etc.

I'm looking for a website redesign/refresh of my current WordPress website. I would like to utilize the same photography, a new photo viewer, and an overall refresh of the entire design. This will need to be WordPress with simple accessibility to make changes as we add additional properties and make updates. We auction luxury real estate and luxury yachts for non-distressed sellers. It needs to be simple, luxurious and with ease of use for both web and especially mobile. www.BrindleHarrow.com

```html
<!DOCTYPE html>
<html lang="en">
<head>
<meta charset="utf-8">
<title>Brindle Harrow — Real Estate &amp; Yachts</title>
<link href="https://fonts.googleapis.com/css2?family=Cormorant+Garamond:wght@500;600&family=EB+Garamond:wght@400;500&family=Poppins:wght@400&display=swap" rel="stylesheet">
<style>
:root{
  --tan:#ab9d7d;
  --tan-dark:#9c8d6c;
  --white:#ffffff;
  --ink:#222222;
  --black:#000000;
  --sky:#7ea3c9;
  --water:#3b5f86;
}
*{margin:0;padding:0;box-sizing:border-box}
html,body{width:1200px;height:3544px;overflow:hidden;background:var(--white)}
body{position:relative;font-family:"EB Garamond",Georgia,serif;color:var(--ink)}
.abs{position:absolute}
.display{font-family:"Cormorant Garamond",Georgia,serif;font-weight:500}
.btn{position:absolute;display:flex;align-items:center;justify-content:center;border-radius:22px;font-family:"EB Garamond",Georgia,serif;font-size:17px;text-decoration:none}
.btn-light{background:var(--white);color:var(--tan)}
.btn-tan{background:var(--tan);color:var(--white)}
.ring{position:absolute;border-radius:50%;border:2px solid currentColor}

/* header */
.site-header{left:0;top:0;width:1200px;height:84px;background:var(--tan)}
.brand{left:112px;top:6px;display:flex;align-items:center;gap:12px;color:var(--white)}
.brand .mark{position:relative;width:72px;height:72px;border:3px solid var(--white);border-radius:50%}
.brand span{font-family:"Cormorant Garamond",serif;font-size:22px;font-weight:500;color:var(--white)}
.nav a{position:absolute;top:33px;font-size:14px;letter-spacing:1px;color:var(--white);text-decoration:none;font-family:"EB Garamond",serif}

/* hero */
.hero{left:0;top:84px;width:1200px;height:589px;background:linear-gradient(180deg,#6f9bc9 0%,#b9cde0 35%,#c9b48a 55%,#5d6e3f 72%,#2e4f74 82%,#1f3a5c 100%)}
.hero-mark{left:564px;top:181px;width:70px;height:70px;color:var(--white)}
.hero-title{left:0;top:250px;width:1200px;text-align:center;color:var(--white);font-size:74px;line-height:86px}
.dots{left:565px;top:599px;display:flex;gap:12px;align-items:center}
.dots i{display:block;width:8px;height:8px;border-radius:50%;background:rgba(255,255,255,.6)}
.dots i:first-child{width:16px;height:16px;background:var(--white)}

/* intro */
.photo{position:absolute}
.intro-mark{left:673px;top:783px;width:48px;height:48px;color:var(--tan)}
.intro-box{left:483px;top:845px;width:604px;height:340px;background:rgba(171,157,125,.97);padding:36px 36px 0 36px;color:var(--white)}
.intro-box h2{font-size:38px;line-height:47px;font-weight:500}
.intro-box p{margin-top:20px;font-size:13px;line-height:26px}

/* sold */
.section-title{left:0;width:1200px;text-align:center;color:var(--tan);font-size:38px}
.sold-copy{left:182px;top:1328px;width:836px;text-align:center;font-size:13.5px;line-height:26px;color:var(--ink)}
.card-img{position:absolute;top:1533px;width:313px;height:208px}
.card-label{position:absolute;top:1708px;width:223px;height:69px;background:var(--tan);color:var(--white);text-align:center;font-family:"Cormorant Garamond",serif;font-size:25px;line-height:30px;padding-top:5px}
.arrow{position:absolute;top:1626px}

/* featured */
.featured{left:0;top:1867px;width:1200px;height:538px;background:var(--tan)}
.featured h2{position:absolute;top:58px;left:0;width:1200px;text-align:center;color:var(--white);font-size:29px}
.featured p{position:absolute;top:112px;left:240px;width:720px;text-align:center;color:var(--white);font-size:13.5px;line-height:27px}
.press{position:absolute;top:298px;width:173px;height:173px;border-radius:50%;background:var(--white);display:flex;align-items:center;justify-content:center;text-align:center;color:#555;font-family:"Cormorant Garamond",serif;font-weight:600;font-size:24px;line-height:24px}

/* about */
.about-mark{left:481px;top:2503px;width:48px;height:48px;color:var(--tan)}
.about-box{left:111px;top:2563px;width:604px;height:342px;background:rgba(171,157,125,.96);padding:48px 36px 0 36px;color:var(--white)}
.about-box h2{font-size:38px;font-weight:500}
.about-box p{margin-top:18px;font-size:13.5px;line-height:26px}

/* upcoming + footer */
.footer{left:0;top:3092px;width:1200px;height:452px;background:var(--black)}
.upcoming{left:111px;top:2989px;width:977px;height:213px;background:var(--tan)}
.upcoming h2{position:absolute;top:46px;width:977px;text-align:center;color:var(--white);font-size:38px}
.f-head{position:absolute;top:3252px;color:var(--white);font-family:"EB Garamond",serif;font-size:19px}
.field{position:absolute;left:113px;width:286px;height:38px;border:1px solid var(--white);color:var(--white);font-size:11px;padding:11px 10px}
.links{position:absolute;left:596px;top:3296px;list-style:none;color:var(--white);font-size:12.5px;line-height:22.5px}
.socials{position:absolute;left:945px;top:3294px;display:flex;gap:22px}
.socials i{display:block;width:20px;height:20px;border-radius:50%;background:var(--white)}
.rule{left:0;top:3491px;width:1200px;height:1px;background:rgba(255,255,255,.6)}
.legal{left:0;top:3508px;width:1200px;text-align:center;color:var(--white);font-family:"Poppins",sans-serif;font-size:13px}
.legal span{margin:0 12px}
</style>
</head>
<body>

<header class="abs site-header">
  <div class="abs brand"><div class="mark"></div><span>Brindle Harrow</span></div>
  <nav class="nav">
    <a style="left:537px">BUY</a>
    <a style="left:614px">SELL</a>
    <a style="left:694px">ABOUT</a>
    <a style="left:794px">CONTACT</a>
  </nav>
  <a class="btn btn-light" style="left:916px;top:21px;width:171px;height:41px">Contact Us</a>
</header>

<section class="abs hero" role="img" aria-label="Waterfront Mediterranean estate with palm trees and a canal in front">
</section>
<div class="ring hero-mark"></div>
<h1 class="abs display hero-title">Brindle Harrow<br>Real Estate &amp; Yachts</h1>
<a class="btn btn-light" style="left:515px;top:443px;width:170px;height:41px">Contact Us</a>
<div class="abs dots"><i></i><i></i><i></i><i></i></div>

<div class="photo" role="img" aria-label="Aerial view of a brick waterfront mansion with a pool at dusk" style="left:111px;top:772px;width:547px;height:330px;background:linear-gradient(160deg,#6f7f93 0%,#8a8f7c 30%,#3f5a2e 60%,#516b38 100%)"></div>
<div class="ring intro-mark"></div>
<div class="abs intro-box">
  <h2 class="display">Over One Billion Dollars of Auctions Marketed Real Estate &amp; Yachts</h2>
  <p>The experience of hearing the auctioneer's final proclamation of “SOLD!” is unparalleled. Whether it's the initial meeting with the seller at their estate or yacht, or the triumphant raising of the paddle by the winning buyer, we relish every moment of the process and the ensuing festivities. We're confident that you will, too.</p>
</div>

<h2 class="abs display section-title" style="top:1265px">Sold by Brindle Harrow</h2>
<p class="abs sold-copy">Brindle Harrow is a top-tier destination for luxury property auctions, having overseen the auction marketing of numerous high-end estates and yachts. Our team of luxury home auction experts is committed to helping property owners obtain the best value for their assets while ensuring a timely sale. Whether you have an expansive compound or a metropolitan penthouse, Brindle Harrow has the necessary skills and expertise to facilitate various luxury real estate auctions.</p>
<a class="btn btn-tan" style="left:515px;top:1453px;width:171px;height:41px">Read More</a>

<svg class="arrow" style="left:70px" width="18" height="24" viewBox="0 0 18 24"><path d="M13 3 L5 12 L13 21" fill="none" stroke="#333" stroke-width="2.5"/></svg>
<svg class="arrow" style="left:1112px" width="18" height="24" viewBox="0 0 18 24"><path d="M5 3 L13 12 L5 21" fill="none" stroke="#333" stroke-width="2.5"/></svg>

<div class="card-img" role="img" aria-label="Aerial view of a wooded peninsula surrounded by water" style="left:111px;background:linear-gradient(180deg,#a8bccc 0%,#3f6786 40%,#2c5270 100%)"></div>
<div class="card-label" style="left:156px">Grasonville -<br>Maryland</div>
<div class="card-img" role="img" aria-label="Mediterranean villa with palm trees and a paver driveway at sunset" style="left:443px;background:linear-gradient(180deg,#c79a8b 0%,#d7c3a3 35%,#3e5a30 70%,#6d5847 100%)"></div>
<div class="card-label" style="left:488px">Naples -<br>Florida</div>
<div class="card-img" role="img" aria-label="Marina with white yachts beneath green hills" style="left:775px;background:linear-gradient(180deg,#9cc2e2 0%,#8aa255 40%,#2f6f8f 65%,#1f5d80 100%)"></div>
<div class="card-label" style="left:820px">Sanibel -<br>Florida</div>

<section class="abs featured">
  <h2 class="display">As Featured In</h2>
  <p>By offering top-tier properties and vessels globally, along with strategic auction dates, exceptional marketing tactics, and a diligent public relations team, even the most prominent media outlets have taken notice. Check out some of our latest press features.</p>
  <a class="btn btn-light" style="left:515px;top:212px;width:171px;height:42px">View Press</a>
  <div class="press" style="left:113px">The Harbor<br>Ledger</div>
  <div class="press" style="left:314px">Meridian</div>
  <div class="press" style="left:514px">Estate<br>Gazette</div>
  <div class="press" style="left:714px">Keel<br>Business</div>
  <div class="press" style="left:914px">Bayline<br>News</div>
</section>

<div class="photo" role="img" aria-label="White motor yacht on blue water under a cloudy sky" style="left:542px;top:2491px;width:545px;height:331px;background:linear-gradient(180deg,#5a8fd0 0%,#b7cde6 40%,#e9edf0 55%,#2c4870 75%,#3f6fa8 100%)"></div>
<div class="ring about-mark"></div>
<div class="abs about-box">
  <h2 class="display">About Us</h2>
  <p>Have you ever experienced a sense of purpose in your life? I consider myself fortunate enough to have felt it not once, but twice. At the age of 18, I realized my first calling as a Paratrooper in the US Army. Although I enjoyed being a Paratrooper, I knew it couldn't last forever. After completing my service, I ventured into the advertising industry.</p>
  <a class="btn btn-light" style="left:36px;top:245px;width:171px;height:41px">View Press</a>
</div>

<footer class="abs footer"></footer>
<section class="abs upcoming">
  <h2 class="display">Upcoming Auctions</h2>
  <a class="btn btn-light" style="left:404px;top:121px;width:171px;height:41px">Browse</a>
</section>

<h3 class="f-head" style="left:111px">Sign Up For Brindle Alerts</h3>
<div class="field" style="top:3296px">Name</div>
<div class="field" style="top:3342px">Email Address</div>
<a class="btn btn-light" style="left:111px;top:3393px;width:144px;height:43px">Submit</a>

<h3 class="f-head" style="left:596px">Quick Links</h3>
<ul class="links"><li>Home</li><li>Buy</li><li>Sell</li><li>About</li><li>Blog</li><li>Contact</li></ul>

<h3 class="f-head" style="left:948px">Follow Along</h3>
<div class="socials" aria-label="Social media links"><i></i><i></i><i></i><i></i></div>
<div class="abs" role="img" aria-label="Service badge" style="left:952px;top:3338px;width:58px;height:58px;border-radius:50%;background:var(--white)"></div>

<div class="abs rule"></div>
<div class="abs legal"><span>Terms of Service</span>|<span>Copyright Policy</span>|<span>Privacy Policy</span></div>

</body>
</html>
```